Copper Lantern

Need a business card for our restaurant. Restaurant and Bar in the mountains of North Idaho. Rustic looking card

rustic design, wood and metal looking, primarily neutral colors

• Name, address, phone number, website, email address

```html
<!DOCTYPE html>
<html lang="en">
<head>
<meta charset="utf-8">
<title>Copper Lantern – Business Card</title>
<link href="https://fonts.googleapis.com/css2?family=Montserrat:wght@400;500;700&display=swap" rel="stylesheet">
<style>
  :root {
    --backdrop: #1c1c1c;
    --card: #141414;
    --card-edge: #262626;
    --ink: #f2f2f2;
    --ink-soft: #cfcfcf;
    --pattern-dark: #0c0c0c;
    --pattern-mid: #2a2a2a;
    --pattern-light: #8a8a8a;
  }
  * { margin: 0; padding: 0; box-sizing: border-box; }
  html, body {
    width: 1200px; height: 875px; overflow: hidden;
    background: var(--backdrop);
    font-family: "Montserrat", sans-serif;
    color: var(--ink);
  }
  .stage {
    position: relative; width: 1200px; height: 875px;
    display: flex; align-items: center; justify-content: center; gap: 60px;
  }
  .card {
    position: relative; width: 500px; height: 290px;
    border-radius: 18px; background: var(--card);
    border: 1px solid var(--card-edge);
    box-shadow: 0 18px 40px rgba(0,0,0,.55);
    overflow: hidden;
  }
  /* Back side: repeated brand pattern */
  .card-back .pattern {
    position: absolute; inset: 0;
    background: linear-gradient(120deg, var(--pattern-light) 0%, var(--pattern-mid) 35%, var(--pattern-dark) 70%, var(--pattern-dark) 100%);
  }
  .card-back .brand-mark {
    position: absolute; left: 300px; top: 130px;
    display: flex; align-items: center; gap: 8px;
    font-size: 14px; font-weight: 700; letter-spacing: .04em;
  }
  .brand-dot { width: 10px; height: 10px; border-radius: 50%; background: var(--ink); }

  /* Front side: contact details */
  .badge {
    position: absolute; left: 188px; top: 26px;
    width: 124px; height: 124px; border-radius: 50%;
    border: 3px solid var(--ink);
    display: flex; align-items: center; justify-content: center; text-align: center;
  }
  .badge-name { font-size: 15px; font-weight: 700; line-height: 1.2; }
  .person {
    position: absolute; right: 268px; top: 172px; text-align: right;
  }
  .person-name { font-size: 21px; font-weight: 700; }
  .person-role { font-size: 11px; font-weight: 400; color: var(--ink-soft); margin-top: 2px; }
  .divider {
    position: absolute; left: 246px; top: 166px; width: 1px; height: 58px; background: var(--ink-soft);
  }
  .contacts {
    position: absolute; left: 260px; top: 162px; list-style: none;
    font-size: 11.5px; line-height: 21px;
  }
  .contacts li { display: flex; align-items: center; gap: 8px; }
  .contacts svg { width: 12px; height: 12px; fill: var(--ink); }
  .address {
    position: absolute; left: 0; right: 0; top: 246px; text-align: center;
    font-size: 11.5px;
  }
</style>
</head>
<body>
<main class="stage">
  <section class="card card-back">
    <div class="pattern" role="img" aria-label="Repeating brand emblem pattern with a glossy highlight"></div>
    <div class="brand-mark"><span class="brand-dot"></span>Copper Lantern</div>
  </section>

  <section class="card card-front">
    <div class="badge"><span class="badge-name">Copper<br>Lantern</span></div>
    <div class="person">
      <p class="person-name">Ellis Harlow</p>
      <p class="person-role">Managing Director</p>
    </div>
    <div class="divider"></div>
    <ul class="contacts">
      <li><svg viewBox="0 0 24 24"><path d="M6.6 10.8a15.5 15.5 0 0 0 6.6 6.6l2.2-2.2a1 1 0 0 1 1-.25 11.4 11.4 0 0 0 3.6.57 1 1 0 0 1 1 1V20a1 1 0 0 1-1 1A17 17 0 0 1 3 4a1 1 0 0 1 1-1h3.5a1 1 0 0 1 1 1c0 1.25.2 2.45.57 3.6a1 1 0 0 1-.25 1z"/></svg>(555) 014 7720</li>
      <li><svg viewBox="0 0 24 24"><path d="M2 5h20v14H2z M2 5l10 8 10-8" fill="none" stroke="#f2f2f2" stroke-width="2"/></svg>hello@copperlantern.com</li>
      <li><svg viewBox="0 0 24 24"><circle cx="12" cy="12" r="10"/></svg>www.copperlantern.com</li>
    </ul>
    <p class="address">48 Pine Ridge Road, Maple Hollow, USA</p>
  </section>
</main>
</body>
</html>
```